4th Generation Family Business Needs a New Card Design!

We are a family owned 4th Generation company. We are based in the Sydney, Australia area and we are desperately in need of a more modern and classy card. We are monumental masons who design, supply & erect lasting memorials throughout cemeteries in Sydney. Our customers are normally in a period of grieving. I have attached logo files that will need to be implemented on the card. Company was established 1935. Australian Owned and Operated. Card needs to be designed to PIXO.com specification.

Target Market(s)

Our target market is based upon people that a grieving for family members that have passed away. We also deal with alot of companies that own and operate cemeteries.

Industry/Entity Type

Business

Contact Information for Business Card

Simon Harcourt, Operations Manager, 0417293086, simon@harcourtmemorials.com.au
Lewis Harcourt, Director, 0491630572, lewis@harcourtmemorials.com.au
Phone # 02 9561 3048
Website: www.harcourtmemorials.com.au
Address: Suite 17, 8 Palfrey Lane, West Carlow, Sydney NSW 2156

Font styles to use
Serif
Decorative
Script

Requirements
Must have
• Would like to see the logo nicely implemented with a modern design. Embossed lettering would be a nice additive.

```html
<!DOCTYPE html>
<html lang="en">
<head>
<meta charset="UTF-8">
<title>Harcourt Memorials – Business Card</title>
<link href="https://fonts.googleapis.com/css2?family=Roboto:wght@400;700&display=swap" rel="stylesheet">
<style>
  :root {
    --backdrop: #1c1f24;
    --card: #161616;
    --card-edge: #0c0c0c;
    --ink-light: #e9e9e9;
    --ink-soft: #b9b9b9;
    --accent-gold: #f2b705;
    --silver: #a9a9ab;
    --web-grey: #8a8a8a;
  }
  html, body {
    margin: 0;
    padding: 0;
    width: 1200px;
    height: 900px;
    overflow: hidden;
    background: var(--backdrop);
    font-family: "Roboto", Arial, sans-serif;
  }
  .stage {
    position: relative;
    width: 1200px;
    height: 900px;
  }
  .card {
    position: absolute;
    width: 560px;
    height: 320px;
    background: linear-gradient(160deg, #1d1d1d 0%, var(--card) 60%, #121212 100%);
    box-shadow: 0 3px 0 var(--card-edge), 0 6px 0 #101010, 0 18px 40px rgba(0,0,0,0.55);
    border-radius: 2px;
    overflow: hidden;
  }
  .card--front { left: 110px; top: 470px; }
  .card--back  { left: 530px; top: 90px; }

  .holder { position: absolute; left: 34px; top: 30px; }
  .holder__name {
    margin: 0;
    font-size: 25px;
    font-weight: 700;
    color: var(--ink-light);
    letter-spacing: 0.2px;
  }
  .holder__surname { color: var(--accent-gold); }
  .holder__role {
    margin: 4px 0 0;
    font-size: 14px;
    color: var(--ink-light);
  }

  .contact { position: absolute; left: 34px; top: 150px; }
  .contact__label {
    margin: 0 0 6px;
    font-size: 12px;
    font-weight: 700;
    color: var(--accent-gold);
    text-transform: uppercase;
  }
  .contact__line {
    margin: 0 0 3px;
    font-size: 11.5px;
    color: var(--ink-soft);
  }

  .brand {
    position: absolute;
    display: flex;
    align-items: center;
    gap: 10px;
    color: var(--silver);
    font-weight: 400;
    text-transform: uppercase;
    letter-spacing: 2px;
  }
  .card--front .brand { right: 34px; top: 150px; font-size: 17px; }
  .card--back .brand {
    left: 50%; top: 50%;
    transform: translate(-50%, -50%);
    font-size: 24px;
  }
  .brand__square {
    width: 14px; height: 14px;
    background: var(--silver);
  }
  .card--back .brand__square { width: 20px; height: 20px; }

  .website {
    position: absolute;
    right: 34px;
    bottom: 26px;
    margin: 0;
    font-size: 13px;
    color: var(--web-grey);
    letter-spacing: 0.3px;
  }
</style>
</head>
<body>
<main class="stage">
  <section class="card card--back" aria-label="Card back">
    <div class="brand"><span class="brand__square"></span>Harcourt Memorials</div>
  </section>

  <section class="card card--front" aria-label="Card front">
    <div class="holder">
      <h1 class="holder__name">Simon <span class="holder__surname">Harcourt</span></h1>
      <p class="holder__role">Operation Manager (0417293086)</p>
    </div>
    <div class="contact">
      <p class="contact__label">Contact</p>
      <p class="contact__line">02 9561 3048</p>
      <p class="contact__line">simon@harcourtmemorials.com.au</p>
      <p class="contact__line">Suite 17, 8 Palfrey Lane, West Carlow, Sydney NSW 2156</p>
    </div>
    <div class="brand"><span class="brand__square"></span>Harcourt Memorials</div>
    <p class="website">www.harcourtmemorials.com.au</p>
  </section>
</main>
</body>
</html>
```